Shopify Web-Page "Tiny-ThreadDays

We are building a new business in Switzerland offering premium sewing holiday camps for kids aged 9–14. In enclosed brief outlines our requirements for a complete Shopify homepage design and a multilingual logo creation.
Domains: tiny-threaddays.ch ; tiny-giornifilo.ch ; tiny-fadentage.ch

Project Overview
We are looking for:
1. A modern, fully designed Shopify homepage in English using standard Shopify content blocks (no custom coding), which we can later update ourselves. Supporting Multilanguage (EN, German, Italian).

2. A logo design that includes the brand identity and communicates our multilingual, creative, and child-focused positioning.

All details in enclosed

```html
<!DOCTYPE html>
<html lang="en">
<head>
<meta charset="utf-8">
<title>Tiny-ThreadDays – Sewing Holiday Camps</title>
<link href="https://fonts.googleapis.com/css2?family=Lora:wght@500;600;700&family=Poppins:wght@400;500;600&display=swap" rel="stylesheet">
<style>
:root{
  --navy:#1d2b4f;
  --pink:#e5096d;
  --orange:#f9a22a;
  --orange-dark:#f08a24;
  --blue:#2f48e0;
  --step-blue:#2a45c8;
  --green:#2f9b3c;
  --green-dark:#1f7a2b;
  --peach:#f6c98a;
  --grey-bg:#f3f3f3;
  --field:#efefef;
  --text:#3a3a3a;
  --muted:#555;
  --footer:#232323;
  --white:#fff;
}
*{box-sizing:border-box;margin:0;padding:0}
html,body{width:1200px;height:4882px;overflow:hidden}
body{font-family:"Poppins",sans-serif;color:var(--text);background:var(--white);position:relative}
.serif{font-family:"Lora",serif}
h1,h2,h3{font-family:"Lora",serif;font-weight:600}
.section-title{text-align:center;color:var(--navy);font-size:38px}

/* top bar */
.topbar{height:42px;background:#ececec;font-size:12px;color:#333;display:flex;align-items:center;justify-content:center}
/* header */
.header{height:82px;display:flex;align-items:center;padding:0 72px 0 74px;border-bottom:1px solid #e6e6e6}
.brand{display:flex;align-items:center;gap:12px;width:290px}
.brand-dot{width:56px;height:56px;border-radius:50%;background:#fbe3ee}
.brand-name{font-family:"Lora",serif;font-weight:700;font-size:24px;color:var(--navy)}
.nav{display:flex;gap:30px;font-size:14px;color:#333;margin-left:16px}
.nav .active{color:var(--pink);font-weight:500}
.header-tools{margin-left:auto;display:flex;align-items:center;gap:22px;font-size:15px;color:#222}
.header-tools span{display:flex;align-items:center;gap:6px}

/* hero */
.hero{height:596px;position:relative;background:linear-gradient(90deg,#1a1a1a 0%,#4a4a4a 22%,#9a8f86 48%,#c9b8a8 70%,#b7c7bd 100%)}
.hero-photo{position:absolute;inset:0}
.hero-copy{position:absolute;left:75px;top:110px;color:var(--white);width:440px}
.hero-copy .welcome{font-size:46px;line-height:1.1}
.hero-copy .title{font-size:60px;line-height:1.1;margin-bottom:18px}
.hero-copy p{font-size:16px;line-height:1.65;margin-bottom:26px}
.btn{display:inline-block;border-radius:30px;color:var(--white);font-weight:500}
.btn-orange{background:var(--orange);padding:13px 36px;font-size:17px}

/* offerings */
.offerings{height:726px;padding-top:58px}
.cards{display:flex;gap:27px;margin:60px 0 0 74px}
.card{width:514px;height:495px;padding:6px;text-align:center;color:var(--white)}
.card-orange{background:var(--orange)}
.card-pink{background:var(--pink)}
.card-photo{height:236px}
.card h3{font-size:28px;margin:22px 0 14px}
.card p{font-size:14px;line-height:1.65;padding:0 60px;margin-bottom:18px}
.btn-green{background:var(--green);padding:9px 28px;font-size:14px}

/* about */
.about{height:503px;display:flex}
.about-copy{width:616px;background:var(--blue);color:var(--white);padding:82px 0 0 74px}
.about-copy h2{font-size:36px;margin-bottom:26px}
.about-copy p{font-size:14.5px;line-height:1.7;margin-bottom:10px;width:515px}
.about-copy .btn{background:var(--green);padding:16px 34px;font-size:18px;margin-top:24px}
.about-photo{flex:1;background:linear-gradient(160deg,#5a4a3a,#8a6e52 40%,#2e6a4a 70%,#3c4c3e)}

/* how it works */
.how{height:673px;padding-top:52px}
.steps{position:relative;margin-top:34px;height:464px}
.step{position:absolute;background:var(--grey-bg);text-align:center;padding:0 20px}
.step-circle{width:94px;height:94px;border-radius:50%;background:var(--peach);margin:0 auto;display:flex;align-items:center;justify-content:center;font-family:"Lora",serif;font-size:38px;font-weight:600;color:#222}
.step h3{color:var(--step-blue);font-size:26px;margin:10px 0 6px;font-weight:500}
.step p{font-size:14px;line-height:1.7;color:#333}

/* why */
.why{height:406px;background:linear-gradient(180deg,#2b8f34,#1f7a2b);color:var(--white);text-align:center;padding-top:42px;position:relative}
.why h2{font-size:38px;font-weight:500}
.why-items{display:flex;justify-content:space-between;margin:48px 50px 0 70px}
.why-item{width:250px;font-size:14px;line-height:1.65}
.why-item svg{display:block;margin:0 auto 18px}
.dots{position:absolute;left:0;right:0;bottom:48px;display:flex;justify-content:center;gap:10px}
.dots i{width:11px;height:11px;border-radius:50%;background:var(--white)}
.dots i:first-child{background:var(--orange)}

/* faq */
.faq{height:555px;padding-top:90px}
.faq-cols{display:flex;gap:36px;margin:50px 0 0 75px}
.faq-col{width:512px}
.faq-item{border-bottom:1px solid #d8d8d8;padding:10px 0 12px;font-size:15.5px;display:flex;justify-content:space-between;align-items:center;color:#222}
.faq-item .icon{font-size:22px;font-weight:600;line-height:1}
.faq-open{padding:0 0 16px;border-bottom:1px solid #d8d8d8;margin-bottom:4px}
.faq-open .q{color:var(--pink);font-weight:500;font-size:15.5px;display:flex;justify-content:space-between;margin-bottom:10px}
.faq-open p{font-size:13.5px;line-height:1.7;color:#444}

/* newsletter */
.newsletter{height:304px;background:var(--pink);color:var(--white);text-align:center;padding-top:58px}
.newsletter h2{font-size:38px;font-weight:500;margin-bottom:14px}
.newsletter p{font-size:16px;margin-bottom:28px}
.subscribe{width:748px;height:50px;margin:0 auto;display:flex;border-radius:26px;overflow:hidden;background:var(--white)}
.subscribe .field{flex:1;text-align:left;padding:0 22px;display:flex;align-items:center;color:#333;font-size:14px}
.subscribe .go{background:var(--orange);padding:0 20px;display:flex;align-items:center;font-family:"Lora",serif;font-weight:600;font-size:15px}

/* booking */
.booking{height:582px;padding-top:66px}
.booking-form{width:872px;margin:44px auto 0;display:grid;grid-template-columns:1fr 1fr;gap:12px 12px}
.field-box{background:var(--field);border-radius:32px;height:64px;padding:0 24px;display:flex;align-items:center;justify-content:space-between;font-size:13px;color:#333}
.field-message{grid-column:1/3;height:140px;border-radius:36px;align-items:flex-start;padding-top:24px}
.submit{grid-column:1/3;justify-self:center;margin-top:6px;background:var(--orange-dark);color:var(--white);border-radius:30px;width:158px;height:54px;display:flex;align-items:center;justify-content:center;font-family:"Lora",serif;font-weight:600;font-size:16px}

/* footer */
.footer{height:339px;background:var(--footer);color:var(--white);position:relative}
.footer-brand{position:absolute;left:78px;top:160px;display:flex;align-items:center;gap:14px}
.footer-brand .brand-dot{width:70px;height:70px;background:#f7d4e4}
.footer-brand .brand-name{color:var(--white);font-size:30px}
.footer-col{position:absolute;top:72px}
.footer-col h4{font-family:"Lora",serif;font-weight:500;font-size:23px;margin-bottom:14px}
.footer-col li{list-style:none;font-size:14px;line-height:31px}
.footer-col .contact{font-size:14px;line-height:28px}
.social{display:flex;gap:20px;margin-top:4px}
.social i{width:20px;height:20px;border-radius:50%;background:var(--white)}
.copyright{height:74px;background:var(--footer);border-top:1px solid #3b3b3b;color:#ddd;font-size:12px;display:flex;align-items:center;justify-content:center}
</style>
</head>
<body>

<div class="topbar">Sed ut perspiciatis unde omnis iste natus</div>

<header class="header">
  <div class="brand"><span class="brand-dot"></span><span class="brand-name">Tiny-ThreadDays</span></div>
  <nav class="nav">
    <span class="active">Home</span><span>About Us</span><span>How it Works</span><span>Upcoming Camp</span><span>FAQ’s</span><span>Contact Us</span>
  </nav>
  <div class="header-tools">
    <svg width="16" height="16" viewBox="0 0 16 16"><circle cx="6.5" cy="6.5" r="5" fill="none" stroke="#222" stroke-width="2"/><line x1="10.5" y1="10.5" x2="15" y2="15" stroke="#222" stroke-width="2.2"/></svg>
    <svg width="17" height="17" viewBox="0 0 17 17"><circle cx="8.5" cy="8.5" r="8" fill="#222"/><circle cx="8.5" cy="6.5" r="3" fill="#fff"/><path d="M3.5 13.5c1.5-2.5 8.5-2.5 10 0" fill="#fff"/></svg>
    <span><svg width="16" height="16" viewBox="0 0 16 16" fill="none" stroke="#222" stroke-width="1.4"><circle cx="8" cy="8" r="7"/><ellipse cx="8" cy="8" rx="3" ry="7"/><line x1="1" y1="8" x2="15" y2="8"/></svg>En</span>
  </div>
</header>

<section class="hero">
  <div class="hero-photo" role="img" aria-label="Photo of two girls sewing fabric at a sewing machine"></div>
  <div class="hero-copy">
    <h1><span class="welcome">Welcome to</span><br><span class="title">Tiny-ThreadDays</span></h1>
    <p>Excepteur sint occaecat cupidatat non proident, sunt in culpa qui officia deserunt mollit anim id est laborum.</p>
    <span class="btn btn-orange">Book Now</span>
  </div>
</section>

<section class="offerings">
  <h2 class="section-title">Upcoming Camp Offerings</h2>
  <div class="cards">
    <article class="card card-orange">
      <div class="card-photo" role="img" aria-label="Photo of a teacher helping a girl at a sewing machine" style="background:linear-gradient(135deg,#c97a6a,#e9c9b8 50%,#9ab8c0)"></div>
      <h3>Spring Camps</h3>
      <p>Nemo enim ipsam voluptatem quia voluptas sit aspernatur aut odit aut fugit, sed quia consequuntur magni dolores eos sed quia non numquam eius modi tempora incidunt</p>
      <span class="btn btn-green">More Info</span>
    </article>
    <article class="card card-pink">
      <div class="card-photo" role="img" aria-label="Photo of children cutting fabric at a sewing class table" style="background:linear-gradient(135deg,#8a7a6a,#d8cfc4 50%,#b9a490)"></div>
      <h3>Summer Camps</h3>
      <p>Nemo enim ipsam voluptatem quia voluptas sit aspernatur aut odit aut fugit, sed quia consequuntur magni dolores eos sed quia non numquam eius modi tempora incidunt</p>
      <span class="btn btn-green">More Info</span>
    </article>
  </div>
</section>

<section class="about">
  <div class="about-copy">
    <h2>About Tiny-ThreadDays</h2>
    <p>Mara and Lina have over 10 years of experience in teaching children sewing, tailoring, and design with fun, style, and structure.</p>
    <p>In small groups (max. 8 children), we guide young talents through a creative week of vacation – with real results: self-sewn pieces, new friends, and lots of pride.</p>
    <p>At the last day, the children show off their success, their own sewn unique pieces, in a sympathetic fashion show.</p>
    <span class="btn">Read More</span>
  </div>
  <div class="about-photo" role="img" aria-label="Photo of students and a teacher working with fabric at a workshop table"></div>
</section>

<section class="how">
  <h2 class="section-title">How the Camp Works</h2>
  <div class="steps">
    <div class="step" style="left:75px;top:0;width:422px;height:464px;padding-top:116px">
      <div class="step-circle">1</div>
      <h3>Project Selection</h3>
      <p>Your child chooses their own model<br>based on previously produced clothing items and sewing patterns.</p>
    </div>
    <div class="step" style="left:521px;top:0;width:291px;height:220px;padding-top:20px">
      <div class="step-circle">2</div>
      <h3>Fabric Selection</h3>
      <p>High-quality fabrics are available.</p>
    </div>
    <div class="step" style="left:837px;top:0;width:291px;height:220px;padding-top:20px">
      <div class="step-circle">3</div>
      <h3>Sewing Machine</h3>
      <p>operation – Learn how to use a sewing machine</p>
    </div>
    <div class="step" style="left:521px;top:244px;width:291px;height:220px;padding-top:18px">
      <div class="step-circle">4</div>
      <h3>Sewing &amp; Refining</h3>
      <p>Step by step to the goal with professional guidance</p>
    </div>
    <div class="step" style="left:837px;top:244px;width:291px;height:220px;padding-top:18px">
      <div class="step-circle">5</div>
      <h3>Showtime!</h3>
      <p>Fashion show or photo shoot at the end of the week</p>
    </div>
  </div>
</section>

<section class="why" role="img" aria-label="Green tinted photo of a sewing workshop behind the section">
  <h2>Why Parents Choose Us</h2>
  <div class="why-items">
    <div class="why-item">
      <svg width="60" height="54" viewBox="0 0 60 54" fill="none" stroke="#fff" stroke-width="2"><circle cx="30" cy="12" r="6"/><circle cx="14" cy="18" r="5"/><circle cx="46" cy="18" r="5"/><path d="M20 40c0-8 4-14 10-14s10 6 10 14"/><path d="M5 42c0-7 4-12 9-12s7 3 8 6"/><path d="M55 42c0-7-4-12-9-12s-7 3-8 6"/><line x1="4" y1="48" x2="56" y2="48"/></svg>
      Small groups &amp;<br>personalized attention
    </div>
    <div class="why-item">
      <svg width="54" height="54" viewBox="0 0 54 54" fill="none" stroke="#fff" stroke-width="2"><circle cx="27" cy="27" r="22"/><ellipse cx="27" cy="27" rx="9" ry="22"/><line x1="5" y1="27" x2="49" y2="27"/><line x1="9" y1="15" x2="45" y2="15"/><line x1="9" y1="39" x2="45" y2="39"/></svg>
      Multilingual supervision<br>(DE / EN / IT)
    </div>
    <div class="why-item">
      <svg width="54" height="54" viewBox="0 0 54 54" fill="none" stroke="#fff" stroke-width="2"><rect x="6" y="6" width="28" height="34"/><rect x="13" y="11" width="28" height="34"/><rect x="20" y="16" width="28" height="34"/><line x1="26" y1="24" x2="42" y2="24"/><line x1="26" y1="31" x2="42" y2="31"/><line x1="26" y1="38" x2="42" y2="38"/></svg>
      High-quality fabrics &amp;<br>top-quality sewing machines<br>(Stitchwell)
    </div>
    <div class="why-item">
      <svg width="54" height="54" viewBox="0 0 54 54" fill="none" stroke="#fff" stroke-width="2"><path d="M10 48l10-18 6 4-8 16z"/><path d="M44 48l-10-18-6 4 8 16z"/><path d="M20 30l7-14 7 14"/><line x1="27" y1="4" x2="27" y2="10"/><line x1="17" y1="8" x2="20" y2="13"/><line x1="37" y1="8" x2="34" y2="13"/></svg>
      Encouragement of<br>creativity, self-confidence,<br>and fine motor skills
    </div>
  </div>
  <div class="dots"><i></i><i></i></div>
</section>

<section class="faq">
  <h2 class="section-title">FAQ’s</h2>
  <div class="faq-cols">
    <div class="faq-col">
      <div class="faq-open">
        <div class="q"><span>Does my child need any prior knowledge?</span><span>—</span></div>
        <p>Nemo enim ipsam voluptatem quia voluptas sit aspernatur aut odit aut fugit, sed quia consequuntur magni dolores eos qui ratione voluptatem sequi nesciunt.</p>
      </div>
      <div class="faq-item"><span>How does the pick-up service work?</span><span class="icon">+</span></div>
      <div class="faq-item"><span>How many items of clothing are produced?”</span><span class="icon">+</span></div>
      <div class="faq-item"><span>Neque porro quisquam estqui dolorem ipsum quia?</span><span class="icon">+</span></div>
      <div class="faq-item"><span>Sit ametconsectetur, adipisci velit?</span><span class="icon">+</span></div>
    </div>
    <div class="faq-col">
      <div class="faq-open">
        <div class="q"><span>Does my child need any prior knowledge?</span><span>—</span></div>
        <p>Nemo enim ipsam voluptatem quia voluptas sit aspernatur aut odit aut fugit, sed quia consequuntur magni dolores eos qui ratione voluptatem sequi nesciunt.</p>
      </div>
      <div class="faq-item"><span>How does the pick-up service work?</span><span class="icon">+</span></div>
      <div class="faq-item"><span>How many items of clothing are produced?”</span><span class="icon">+</span></div>
      <div class="faq-item"><span>Neque porro quisquam estqui dolorem ipsum quia?</span><span class="icon">+</span></div>
      <div class="faq-item"><span>Sit ametconsectetur, adipisci velit?</span><span class="icon">+</span></div>
    </div>
  </div>
</section>

<section class="newsletter">
  <h2>Newsletter Sign Up</h2>
  <p>Excepteur sint occaecat cupidatat non proident &nbsp;enim ipsam voluptatem quia.</p>
  <div class="subscribe"><span class="field">Email Address</span><span class="go">Subscribe Now</span></div>
</section>

<section class="booking">
  <h2 class="section-title">Camp Booking</h2>
  <div class="booking-form">
    <div class="field-box">Name</div>
    <div class="field-box">Email Address</div>
    <div class="field-box">Phone No</div>
    <div class="field-box">Select Date
      <svg width="12" height="12" viewBox="0 0 12 12"><rect x="1" y="2" width="10" height="9" fill="#444"/><rect x="2" y="5" width="8" height="5" fill="#efefef"/></svg>
    </div>
    <div class="field-box field-message">Message</div>
    <div class="submit">Submit</div>
  </div>
</section>

<footer class="footer">
  <div class="footer-brand"><span class="brand-dot"></span><span class="brand-name">Tiny-ThreadDays</span></div>
  <div class="footer-col" style="left:404px">
    <h4>Navigations</h4>
    <ul><li>Home</li><li>About Us</li><li>How it Works</li><li>Upcoming Camp</li><li>FAQ’s</li><li>Contact Us</li></ul>
  </div>
  <div class="footer-col" style="left:635px">
    <h4>Contact Us</h4>
    <div class="contact">14 Seeweg,<br>8002 Zurich, Switzerland<br>+41 44 555 01 23<br>hello@tiny-threaddays.ch</div>
  </div>
  <div class="footer-col" style="left:916px">
    <h4>Social With Us</h4>
    <div class="social"><i></i><i></i><i></i><i></i><i></i></div>
  </div>
</footer>
<div class="copyright">Copyrights© 2025 Tiny-ThreadDays All Rights Reserved</div>

</body>
</html>
```